Theme and starter template for small business powerpoint deck

We are starting a technology consulting company and would like to have a powerpoint/google slide theme and initial template. We are more concerned with the theme/colors at this point. Initial template can be pretty simple. We would want a cover slide, agenda slide, some content slides including text content, image content, a combination of both, etc. A closing slide. we have included jpg files of our logo, let us know if you would prefer eps/vector. I assume you may want exact color data as well?

Target Market(s)

Technology and Customer Experience Leadership at companies with 25 or more employees

Industry/Entity Type

Technology Consulting

Font styles to use
Sans Serif

Colors
0054AA
0677BA
7BADD7
CADEEF
E8F1F8

Requirements
Must have
• I have attached JPG and EPS and vector files to project. I would like to stay with those colors but open to slight variation if recommended.

```html
<!DOCTYPE html>
<html lang="en">
<head>
<meta charset="utf-8">
<title>Vantrelis Slide Theme</title>
<link href="https://fonts.googleapis.com/css2?family=Poppins:wght@400;500;600;700&display=swap" rel="stylesheet">
<style>
:root{
  --stage:#c9c9c9;
  --brand:#0054AA;
  --brand-mid:#0677BA;
  --brand-soft:#7BADD7;
  --brand-pale:#CADEEF;
  --brand-mist:#E8F1F8;
  --title-accent:#3d63d6;
  --navy:#0b2d6e;
  --ink:#333a45;
  --muted:#6b7280;
  --accent-red:#d23a3f;
  --white:#ffffff;
  --rule:#d4d8de;
}
*{margin:0;padding:0;box-sizing:border-box}
html,body{width:1200px;height:410px;overflow:hidden}
body{background:var(--stage);position:relative;font-family:'Poppins',sans-serif;color:var(--ink)}
.slide-frame{position:absolute;width:245px;height:137.5px;overflow:hidden}
.slide{position:absolute;left:0;top:0;width:525px;height:295px;transform:scale(0.4667);transform-origin:0 0;background:var(--white);overflow:hidden}
.slide--blue{background:linear-gradient(135deg,#0a4ea6 0%,var(--brand) 55%,#0a4a9c 100%)}
.abs{position:absolute}
.brand-word{position:absolute;left:23px;top:18px;font-size:20px;font-weight:700;letter-spacing:1px;color:var(--white);display:flex;align-items:center;gap:6px}
.brand-word .dot{width:8px;height:8px;background:var(--white)}
.slide-title{position:absolute;left:23px;top:8px;font-size:20px;font-weight:500;color:var(--navy)}
.slide-title span{color:var(--title-accent)}
.title-rule{position:absolute;left:23px;top:40px;width:55px;height:3px;background:var(--accent-red)}
.footer-mark{position:absolute;left:23px;top:272px;font-size:8px;font-weight:700;color:var(--navy);display:flex;align-items:center;gap:4px;letter-spacing:.5px}
.footer-mark .dot{width:7px;height:7px;background:var(--brand)}
.footer-copy{position:absolute;right:50px;top:270px;font-size:7.5px;color:var(--ink)}
.page-no{position:absolute;right:24px;top:267px;width:15px;height:15px;background:var(--brand);color:var(--white);font-size:7px;display:flex;align-items:center;justify-content:center}
.small{font-size:5.8px;line-height:1.75;color:var(--muted);text-align:justify}
.photo{position:absolute}
/* cover */
.cover-panel{position:absolute;left:0;top:116px;width:336px;height:119px;background:var(--brand-mist)}
.cover-title{position:absolute;left:23px;top:128px;font-size:23px;line-height:1.15;font-weight:600;color:var(--brand)}
.cover-sub{position:absolute;left:23px;top:187px;font-size:10.5px;color:#1a1a1a}
.cover-date{position:absolute;left:23px;top:209px;font-size:6.5px;color:#1a1a1a}
.cover-bar{position:absolute;left:28px;top:232px;width:280px;height:8px;background:#5a6ee0}
/* toc */
.toc-item{position:absolute;width:210px;display:flex;gap:8px}
.toc-num{font-size:18px;color:#a3a8b0;width:18px;text-align:right;border-right:1px solid var(--rule);padding-right:6px;height:32px;line-height:32px;margin-top:6px;box-sizing:content-box}
.toc-head{font-size:12.5px;font-weight:500;color:var(--title-accent)}
.toc-desc{font-size:5.5px;line-height:1.8;color:var(--ink);width:170px}
/* why */
.why-box{position:absolute;left:83px;top:165px;width:207px;height:78px;background:var(--brand);color:var(--white);font-size:6px;line-height:1.9;padding:18px 12px}
/* value */
.value-icon{position:absolute;width:52px;height:46px;border:1px solid var(--rule);display:flex;align-items:center;justify-content:center;background:var(--white)}
.value-head{position:absolute;font-size:12.5px;font-weight:500;color:var(--brand)}
.value-text{position:absolute;width:155px;font-size:5.3px;line-height:1.8;color:var(--ink)}
.value-note{position:absolute;left:80px;top:199px;width:365px;font-size:6px;line-height:1.9;text-align:center;color:var(--ink)}
/* team */
.member{position:absolute;width:140px;text-align:center}
.member-ring{width:105px;height:105px;border-radius:50%;border:3px solid var(--brand);margin:0 auto;background:linear-gradient(180deg,#eceff3,#b9c3cf)}
.member-name{font-size:10.5px;font-weight:500;color:#1a1a1a;margin-top:9px}
.member-role{font-size:9px;color:#1a1a1a}
.team-divider{position:absolute;top:82px;width:1px;height:128px;background:#b9bec6}
/* closing */
.thanks{position:absolute;left:23px;top:104px;font-size:23px;font-weight:700;color:var(--white)}
.thanks-text{position:absolute;left:23px;top:143px;width:240px;font-size:6px;line-height:1.95;color:var(--white);text-align:justify}
.social{position:absolute;top:212px;left:23px;display:flex;gap:8px}
.social span{width:18px;height:18px;border:1px solid var(--white);border-radius:50%}
</style>
</head>
<body>

<!-- Row 1 -->
<div class="slide-frame" style="left:51px;top:51px">
  <section class="slide slide--blue">
    <div class="brand-word">VANTRELIS<span class="dot"></span></div>
    <div class="cover-panel"></div>
    <h1 class="cover-title">Presentation Title<br>Goes Here</h1>
    <p class="cover-sub">Subtitle Of Presentation Goes Here</p>
    <p class="cover-date">Sunday, August 09, 2024</p>
    <div class="cover-bar"></div>
  </section>
</div>

<div class="slide-frame" style="left:335px;top:51px">
  <section class="slide">
    <h2 class="slide-title">Table Of <span>Content</span></h2>
    <div class="title-rule"></div>
    <div class="toc-item" style="left:40px;top:66px"><div class="toc-num">1</div><div><div class="toc-head">Title Goes Here</div><p class="toc-desc">Lorem ipsum dolor sit amet, consectetur adipiscing elit, sed do eiusmod tempor incididunt</p></div></div>
    <div class="toc-item" style="left:270px;top:66px"><div class="toc-num">2</div><div><div class="toc-head">Title Goes Here</div><p class="toc-desc">Lorem ipsum dolor sit amet, consectetur adipiscing elit, sed do eiusmod tempor incididunt</p></div></div>
    <div class="toc-item" style="left:40px;top:122px"><div class="toc-num">3</div><div><div class="toc-head">Title Goes Here</div><p class="toc-desc">Lorem ipsum dolor sit amet, consectetur adipiscing elit, sed do eiusmod tempor incididunt</p></div></div>
    <div class="toc-item" style="left:270px;top:122px"><div class="toc-num">4</div><div><div class="toc-head">Title Goes Here</div><p class="toc-desc">Lorem ipsum dolor sit amet, consectetur adipiscing elit, sed do eiusmod tempor incididunt</p></div></div>
    <div class="toc-item" style="left:40px;top:178px"><div class="toc-num">5</div><div><div class="toc-head">Title Goes Here</div><p class="toc-desc">Lorem ipsum dolor sit amet, consectetur adipiscing elit, sed do eiusmod tempor incididunt</p></div></div>
    <div class="toc-item" style="left:270px;top:178px"><div class="toc-num">6</div><div><div class="toc-head">Title Goes Here</div><p class="toc-desc">Lorem ipsum dolor sit amet, consectetur adipiscing elit, sed do eiusmod tempor incididunt</p></div></div>
    <div class="footer-mark"><span class="dot"></span>VANTRELIS</div>
    <div class="footer-copy">© 2024 Vantrelis. All Rights Reserved.</div>
    <div class="page-no">2</div>
  </section>
</div>

<div class="slide-frame" style="left:620px;top:51px">
  <section class="slide">
    <h2 class="slide-title">About <span>Us</span></h2>
    <div class="title-rule"></div>
    <div class="abs small" style="left:23px;top:72px;width:257px;color:var(--ink)">
      <p>Sed ut perspiciatis unde omnis iste natus error sit voluptatem accusantium doloremque laudantium, totam rem aperiam, eaque ipsa quae ab illo inventore veritatis et quasi architecto beatae vitae dicta sunt explicabo. Nemo enim ipsam voluptatem quia voluptas sit aspernatur aut odit aut fugit, sed quia consequuntur magni dolores eos qui ratione voluptatem sequi nesciunt. Neque porro quisquam est, qui dolorem ipsum quia dolor sit amet, consectetur, adipisci velit, sed quia non numquam eius modi tempora incidunt ut labore et dolore magnam aliquam quaerat voluptatem.</p>
      <p style="margin-top:8px">Lorem ipsum dolor sit amet, consectetur adipiscing elit, sed do eiusmod tempor incididunt ut labore et</p>
    </div>
    <div class="photo" role="img" aria-label="Photo of a team meeting around a conference table" style="left:292px;top:0;width:233px;height:212px;background:linear-gradient(160deg,#dfe6ee,#a9b6c4)"></div>
    <div class="footer-mark"><span class="dot"></span>VANTRELIS</div>
    <div class="footer-copy">© 2024 Vantrelis. All Rights Reserved.</div>
    <div class="page-no">3</div>
  </section>
</div>

<div class="slide-frame" style="left:904px;top:51px">
  <section class="slide">
    <h2 class="slide-title">Why <span>Choose Us</span></h2>
    <div class="title-rule"></div>
    <div class="abs small" style="left:23px;top:54px;width:222px;color:var(--ink)">
      <p>Sed ut perspiciatis unde omnis iste natus error sit voluptatem accusantium doloremque laudantium, totam rem aperiam, eaque ipsa quae ab illo inventore veritatis et quasi architecto beatae vitae dicta sunt explicabo.</p>
      <p style="margin-top:6px">Sed ut perspiciatis unde omnis iste natus error sit voluptatem accusantium doloremque laudantium, totam rem aperiam, eaque ipsa quae ab illo inventore veritatis</p>
    </div>
    <div class="abs small" style="left:278px;top:54px;width:224px;color:var(--ink)">
      <p>Sed ut perspiciatis unde omnis iste natus error sit voluptatem accusantium doloremque laudantium, totam rem aperiam, eaque ipsa quae ab illo inventore veritatis et quasi architecto beatae vitae dicta sunt explicabo.</p>
      <p style="margin-top:6px">Sed ut perspiciatis unde omnis iste natus error sit voluptatem accusantium doloremque laudantium,</p>
    </div>
    <div class="photo" role="img" aria-label="Photo of two colleagues working together at a laptop" style="left:278px;top:143px;width:224px;height:109px;background:linear-gradient(160deg,#eef1f4,#bfc8d2)"></div>
    <div class="why-box">Sed ut perspiciatis unde omnis iste natus error sit voluptatem accusantium doloremque laudantium, totam rem aperiam, eaque ipsa</div>
    <div class="footer-mark"><span class="dot"></span>VANTRELIS</div>
    <div class="footer-copy">© 2024 Vantrelis. All Rights Reserved.</div>
    <div class="page-no">4</div>
  </section>
</div>

<!-- Row 2 -->
<div class="slide-frame" style="left:51px;top:221px">
  <section class="slide">
    <h2 class="slide-title">Our <span>Value</span></h2>
    <div class="title-rule"></div>
    <div class="value-icon" style="left:23px;top:64px"><svg width="26" height="26" viewBox="0 0 26 26" fill="none" stroke="#2a4fb0" stroke-width="1.3"><circle cx="13" cy="13" r="8"/><circle cx="13" cy="13" r="3"/></svg></div>
    <div class="value-head" style="left:89px;top:60px">Content Here</div>
    <p class="value-text" style="left:89px;top:80px">Lorem ipsum dolor sit amet, consectetur adipiscing elit, sed do eiusmod tempor incididunt ut labore et dolore magna aliqua quis ipsum suspendisse</p>
    <div class="value-icon" style="left:282px;top:64px"><svg width="26" height="26" viewBox="0 0 26 26" fill="none" stroke="#2a4fb0" stroke-width="1.3"><circle cx="10" cy="9" r="4"/><path d="M3 22c1-5 4-7 7-7s6 2 7 7"/><path d="M18 12v-4M21 12v-7M24 12v-2"/></svg></div>
    <div class="value-head" style="left:348px;top:60px">Content Here</div>
    <p class="value-text" style="left:348px;top:80px">Lorem ipsum dolor sit amet, consectetur adipiscing elit, sed do eiusmod tempor incididunt ut labore et dolore magna aliqua quis ipsum suspendisse</p>
    <div class="value-icon" style="left:23px;top:132px"><svg width="26" height="26" viewBox="0 0 26 26" fill="none" stroke="#2a4fb0" stroke-width="1.3"><rect x="7" y="7" width="12" height="12" rx="2"/><path d="M10 3v4M16 3v4M10 19v4M16 19v4M3 10h4M3 16h4M19 10h4M19 16h4"/></svg></div>
    <div class="value-head" style="left:89px;top:128px">Content Here</div>
    <p class="value-text" style="left:89px;top:148px">Lorem ipsum dolor sit amet, consectetur adipiscing elit, sed do eiusmod tempor incididunt ut labore et dolore magna aliqua quis ipsum suspendisse</p>
    <div class="value-icon" style="left:282px;top:132px"><svg width="26" height="26" viewBox="0 0 26 26" fill="none" stroke="#2a4fb0" stroke-width="1.3"><circle cx="13" cy="11" r="6"/><path d="M10 17v3h6v-3M11 23h4"/></svg></div>
    <div class="value-head" style="left:348px;top:128px">Content Here</div>
    <p class="value-text" style="left:348px;top:148px">Lorem ipsum dolor sit amet, consectetur adipiscing elit, sed do eiusmod tempor incididunt ut labore et dolore magna aliqua quis ipsum suspendisse</p>
    <p class="value-note">Sed ut perspiciatis unde omnis iste natus error sit voluptatem accusantium doloremque laudantium, totam rem aperiam, eaque ipsa quae ab illo inventore veritatis et quasi architecto beatae vitae dicta sunt explicabo. Nemo enim ipsam voluptatem quia voluptas sit aspernatur aut odit aut fugit, sed quia</p>
    <div class="footer-mark"><span class="dot"></span>VANTRELIS</div>
    <div class="footer-copy">© 2024 Vantrelis. All Rights Reserved.</div>
    <div class="page-no">5</div>
  </section>
</div>

<div class="slide-frame" style="left:335px;top:221px">
  <section class="slide">
    <h2 class="slide-title">Heading <span>Goes Here</span></h2>
    <div class="title-rule"></div>
    <svg class="abs" style="left:20px;top:60px" width="250" height="140" viewBox="0 0 250 140" font-family="Poppins, sans-serif" font-size="6" fill="#1a1a1a" text-anchor="middle">
      <g fill="#fff" stroke="#6b7280" stroke-width="0.8">
        <rect x="15" y="63" width="22" height="55"/>
        <rect x="53" y="42" width="22" height="76"/>
        <rect x="92" y="87" width="22" height="31"/>
        <rect x="130" y="77" width="22" height="41"/>
        <rect x="168" y="42" width="22" height="76"/>
        <rect x="207" y="20" width="22" height="98"/>
      </g>
      <line x1="3" y1="118" x2="243" y2="118" stroke="#9aa0a8" stroke-width="0.8"/>
      <text x="26" y="59">50%</text><text x="64" y="38">70%</text><text x="103" y="83">28%</text>
      <text x="141" y="73">38%</text><text x="179" y="38">70%</text><text x="218" y="16">90%</text>
      <text x="26" y="130">A</text><text x="64" y="130">B</text><text x="103" y="130">C</text>
      <text x="141" y="130">D</text><text x="179" y="130">E</text><text x="218" y="130">F</text>
    </svg>
    <div class="abs small" style="left:287px;top:64px;width:215px;color:var(--ink)">
      <p>Sed ut perspiciatis unde omnis iste natus error sit voluptatem accusantium doloremque laudantium, totam rem aperiam, eaque ipsa quae ab illo inventore veritatis et quasi architecto beatae vitae dicta sunt explicabo. Nemo enim ipsam voluptatem quia voluptas sit aspernatur aut</p>
      <p style="margin-top:8px">Sed ut perspiciatis unde omnis iste natus error sit voluptatem accusantium doloremque laudantium, totam rem aperiam, eaque ipsa quae ab illo inventore veritatis et quasi architecto beatae vitae dicta sunt explicabo. Nemo enim ipsam voluptatem quia voluptas sit aspernatur aut</p>
    </div>
    <div class="footer-mark"><span class="dot"></span>VANTRELIS</div>
    <div class="footer-copy">© 2024 Vantrelis. All Rights Reserved.</div>
    <div class="page-no">6</div>
  </section>
</div>

<div class="slide-frame" style="left:620px;top:221px">
  <section class="slide">
    <h2 class="slide-title">Our <span>Team Member</span></h2>
    <div class="title-rule"></div>
    <div class="member" style="left:18px;top:76px"><div class="member-ring" role="img" aria-label="Portrait photo of team member"></div><div class="member-name">Mara Ellison</div><div class="member-role">Co-Founder</div></div>
    <div class="team-divider" style="left:176px"></div>
    <div class="member" style="left:193px;top:76px"><div class="member-ring" role="img" aria-label="Portrait photo of team member"></div><div class="member-name">Jonas Reed</div><div class="member-role">Co-Founder</div></div>
    <div class="team-divider" style="left:351px"></div>
    <div class="member" style="left:367px;top:76px"><div class="member-ring" role="img" aria-label="Portrait photo of team member"></div><div class="member-name">Owen Hartley</div><div class="member-role">Co-Founder</div></div>
    <div class="footer-mark"><span class="dot"></span>VANTRELIS</div>
    <div class="footer-copy">© 2024 Vantrelis. All Rights Reserved.</div>
    <div class="page-no">7</div>
  </section>
</div>

<div class="slide-frame" style="left:904px;top:221px">
  <section class="slide slide--blue">
    <div class="brand-word">VANTRELIS<span class="dot"></span></div>
    <h2 class="thanks">Thank You !!</h2>
    <p class="thanks-text">Lorem ipsum dolor sit amet, consectetur adipiscing elit, sed do eiusmod tempor incididunt ut labore et dolore magna aliqua. Quis ipsum suspendisse ultrices gravida. Risus commodo viverra maecenas accumsan lacus vel facilisis.</p>
    <div class="social"><span></span><span></span><span></span><span></span><span></span></div>
    <div class="photo" role="img" aria-label="Photo of a smiling man in a yellow jacket holding a phone" style="left:330px;top:45px;width:180px;height:250px;background:linear-gradient(180deg,rgba(123,173,215,.35),rgba(230,170,40,.55))"></div>
  </section>
</div>

</body>
</html>
```